Marcus Delbridge Finance

Need a personal website advertising Equipment Finance,Business Finance,Commercial Finance, Construction Finance, Bridging Finance. Similar websites are www.corvalend.com.au / www.tarmivest.com.au / www.qbr7.com.au /wwwhalvecredit.com.au

Target Market(s)

Business People

Industry/Entity Type

Business

Number of Pages Required

3 page

Font styles to use
Serif
Sans Serif

Requirements
Must have
• All i want is a simple corporate looking website advertising Equipment Finance, Commercial Finance, Construction Finance, Business Finance, Bridging Finance,

```html
<!DOCTYPE html>
<html lang="en">
<head>
<meta charset="utf-8">
<title>Marcus Delbridge Finance</title>
<link rel="stylesheet" href="https://fonts.googleapis.com/css2?family=Arimo:wght@400&family=Open+Sans:wght@400;700&family=Raleway:wght@300;400;700&display=swap">
<style>
:root{
  --gold:#f0b21f;
  --white:#ffffff;
  --ink:#2b2b2b;
  --body:#555555;
  --mist:#ececec;
  --footer:#262626;
  --line:#3a3a3a;
  --field-border:#cfcfcf;
}
*{box-sizing:border-box;margin:0;padding:0}
html,body{width:1200px;height:2866px;overflow:hidden}
body{position:relative;font-family:"Open Sans",sans-serif;color:var(--body);background:var(--white)}
section,header,footer{position:absolute;left:0;width:1200px}
.abs{position:absolute}
.center{left:0;width:1200px;text-align:center}

/* Hero */
.hero{top:0;height:676px;background:linear-gradient(180deg,#5d6b78 0%,#4a525a 35%,#3b3d40 70%,#2e2c2a 100%)}
.hero-photo{position:absolute;inset:0;background:radial-gradient(ellipse at 88% 12%,rgba(255,230,170,.45),transparent 45%),linear-gradient(180deg,rgba(90,110,130,.5),rgba(40,38,35,.6))}
.brand{left:80px;top:28px}
.brand-name{font-family:"Arimo",sans-serif;font-size:54px;line-height:1;color:var(--gold)}
.brand-sub{font-family:"Arimo",sans-serif;font-size:34px;letter-spacing:14px;color:var(--white);margin-top:2px}
.nav{right:82px;top:52px;display:flex;gap:48px;font-family:"Raleway",sans-serif;font-size:21px;color:var(--white)}
.nav .active{color:var(--gold)}
.hero-title{top:246px;font-family:"Raleway",sans-serif;font-weight:700;font-size:40px;line-height:54px;color:var(--white)}
.hero-call{top:374px;display:flex;justify-content:center;align-items:center;gap:14px;font-family:"Open Sans",sans-serif;font-weight:700;font-size:42px;color:var(--gold)}
.hero-call svg{width:56px;height:56px}

/* Welcome */
.welcome{top:676px;height:455px}
.section-title{font-family:"Raleway",sans-serif;font-weight:400;font-size:43px;color:var(--ink)}
.section-title .accent{color:var(--gold);font-weight:300}
.welcome .section-title{top:174px}
.welcome-text{left:130px;width:940px;top:234px;text-align:center;font-size:15.5px;line-height:26px}
.btn{display:flex;align-items:center;justify-content:center;border:1.5px solid var(--gold);border-radius:26px;color:var(--gold);font-family:"Raleway",sans-serif;font-size:20px}
.welcome .btn{left:512px;top:339px;width:176px;height:51px}

/* Services */
.services{top:1131px;height:417px;background:var(--gold);color:var(--white)}
.services .section-title{top:46px;color:var(--white);font-weight:300}
.service{top:121px;width:200px;text-align:center}
.service-icon{width:116px;height:116px;margin:0 auto;border:2px solid var(--white);border-radius:50%;display:flex;align-items:center;justify-content:center}
.service-icon svg{width:62px;height:62px}
.service-name{font-family:"Raleway",sans-serif;font-size:23px;margin-top:18px}
.service-text{font-size:14.5px;line-height:25px;margin-top:4px}

/* Call back */
.callback{top:1548px;height:311px;background:linear-gradient(120deg,#2f3033 0%,#4a4c50 45%,#6c6660 75%,#3a3a3c 100%)}
.callback-photo{position:absolute;inset:0;background:rgba(20,20,22,.45)}
.callback .section-title{top:46px;color:var(--white);font-weight:300}
.callback-text{left:170px;width:860px;top:110px;text-align:center;color:var(--white);font-size:15.5px;line-height:25px}
.callback .btn{left:455px;top:179px;width:290px;height:50px}

/* Testimonials */
.testimonials{top:1859px;height:348px}
.testimonials .section-title{top:58px}
.quote-mark{top:110px;font-family:"Raleway",sans-serif;font-weight:700;font-size:56px;line-height:1;color:#aaaaaa}
.client-photo{width:126px;height:126px;border-radius:50%;border:2px solid var(--gold);background:linear-gradient(160deg,#cfc7bd,#8c8278)}
.client-text{width:370px;font-size:15.5px;line-height:25px}
.client-name{font-size:15px;font-weight:700;color:var(--gold);margin-top:22px}

/* Quote form */
.quote{top:2207px;height:430px;background:var(--mist)}
.quote .section-title{top:49px}
.field{background:var(--white);border:1px solid var(--field-border);font-size:15px;color:#666;padding:10px 10px}
.quote .btn{left:522px;top:315px;width:156px;height:52px}

/* Footer */
.footer{top:2637px;height:229px;background:var(--footer);color:var(--white)}
.footer .brand-name{color:var(--white);font-size:40px}
.footer .brand-sub{font-size:25px;letter-spacing:10px}
.footer-info{left:441px;top:44px;width:290px;font-size:15px;line-height:25px}
.footer-info b{font-weight:700}
.follow-title{left:803px;top:42px;font-family:"Raleway",sans-serif;font-weight:700;font-size:20px}
.social{top:80px;width:46px;height:46px;border-radius:50%;border:2px solid var(--gold)}
.social.filled{background:var(--gold)}
.footer-rule{left:80px;top:176px;width:1040px;height:1px;background:var(--line)}
.copyright{top:191px;font-size:15px}
.copyright b{color:var(--gold)}
</style>
</head>
<body>

<header class="hero">
  <div class="hero-photo" role="img" aria-label="City skyline photograph with sunlight"></div>
  <div class="abs brand">
    <div class="brand-name">Marcus Delbridge</div>
    <div class="brand-sub">Finance</div>
  </div>
  <nav class="abs nav">
    <span class="active">HOME</span><span>ABOUT</span><span>SERVICES</span><span>CONTACT</span>
  </nav>
  <h1 class="abs center hero-title">LOREM IPSUM IS SIMPLY DUMMY<br>TEXT AND PRINTING.</h1>
  <div class="abs center hero-call">
    <span>CALL US</span>
    <svg viewBox="0 0 56 56" aria-hidden="true"><circle cx="28" cy="28" r="26" fill="none" stroke="#fff" stroke-width="2"/><path d="M20 17c2-1 4 3 4 4s-2 2-2 3c1 3 4 6 7 7 1 0 2-2 3-2s5 2 4 4c-1 2-3 3-5 3-7-1-13-7-14-14 0-2 1-4 3-5z" fill="#fff"/></svg>
    <span>123 456 7890</span>
  </div>
</header>

<section class="welcome">
  <h2 class="abs center section-title"><span class="accent">WELCOME TO</span> MARCUS DELBRIDGE FINANCE</h2>
  <p class="abs welcome-text">Lorem Ipsum is dummy text of the printing and typesetting industry. Lorem Ipsum has been the industry's standard dummy text ever since the 1500s, when an unknown printer took a galley of type it to make a type specimen book. It has survived not only five centuries, but also the leap into electronic typesetting, remaining essentially unchanged.</p>
  <div class="abs btn">READ MORE</div>
</section>

<section class="services">
  <h2 class="abs center section-title">SERVICES WE PROVIDE</h2>
  <div class="abs service" style="left:74px">
    <div class="service-icon"><svg viewBox="0 0 62 62" fill="none" stroke="#fff" stroke-width="3"><circle cx="31" cy="31" r="22"/><circle cx="31" cy="31" r="9"/><path d="M31 5v8M31 49v8M5 31h8M49 31h8"/></svg></div>
    <div class="service-name">Equipment</div>
    <p class="service-text">Lorem Ipsum is dummy text of the printing and typesetting industry.</p>
  </div>
  <div class="abs service" style="left:284px">
    <div class="service-icon"><svg viewBox="0 0 62 62" fill="#fff"><rect x="8" y="42" width="9" height="14"/><rect x="21" y="34" width="9" height="22"/><rect x="34" y="38" width="9" height="18"/><rect x="47" y="26" width="9" height="30"/><path d="M8 34l14-12 10 6 18-16" fill="none" stroke="#fff" stroke-width="3"/><path d="M44 8h10v10z"/></svg></div>
    <div class="service-name">Business</div>
    <p class="service-text">Lorem Ipsum is dummy text of the printing and typesetting industry.</p>
  </div>
  <div class="abs service" style="left:498px">
    <div class="service-icon"><svg viewBox="0 0 62 62" fill="none" stroke="#fff" stroke-width="3" stroke-linejoin="round"><path d="M4 24l10-6 10 4 8-4 10 0 16 8"/><path d="M12 30l12 12 6 2 12-10 14-6"/><path d="M24 36l8-8 8 6"/></svg></div>
    <div class="service-name">Commercial</div>
    <p class="service-text">Lorem Ipsum is dummy text of the printing and typesetting industry.</p>
  </div>
  <div class="abs service" style="left:716px">
    <div class="service-icon"><svg viewBox="0 0 62 62" fill="#fff"><rect x="6" y="24" width="14" height="32"/><rect x="22" y="8" width="16" height="48"/><rect x="40" y="18" width="16" height="38"/><g fill="#f0b21f"><rect x="26" y="14" width="3" height="3"/><rect x="32" y="14" width="3" height="3"/><rect x="26" y="22" width="3" height="3"/><rect x="32" y="22" width="3" height="3"/><rect x="26" y="30" width="3" height="3"/><rect x="32" y="30" width="3" height="3"/><rect x="44" y="24" width="3" height="3"/><rect x="50" y="24" width="3" height="3"/><rect x="44" y="32" width="3" height="3"/><rect x="50" y="32" width="3" height="3"/><rect x="10" y="30" width="3" height="3"/><rect x="10" y="38" width="3" height="3"/></g></svg></div>
    <div class="service-name">Construction</div>
    <p class="service-text">Lorem Ipsum is dummy text of the printing and typesetting industry.</p>
  </div>
  <div class="abs service" style="left:928px">
    <div class="service-icon"><svg viewBox="0 0 62 62" fill="none" stroke="#fff" stroke-width="3"><path d="M2 40h58"/><path d="M18 14v34M44 14v34"/><path d="M2 22q16 4 16 -8M18 14q13 24 26 0M44 14q0 12 16 8"/></svg></div>
    <div class="service-name">Bridging</div>
    <p class="service-text">Lorem Ipsum is dummy text of the printing and typesetting industry.</p>
  </div>
</section>

<section class="callback">
  <div class="callback-photo" role="img" aria-label="Photograph of hands typing on a laptop keyboard"></div>
  <h2 class="abs center section-title">REQUEST A CALL BACK</h2>
  <p class="abs callback-text">Lorem Ipsum is dummy text of the printing and typesetting industry. Lorem Ipsum has been the industry's standard dummy text ever since the 1500.</p>
  <div class="abs btn">REQUEST A CALL BACK</div>
</section>

<section class="testimonials">
  <h2 class="abs center section-title"><span class="accent">WHAT OUR</span> CLIENT SAY</h2>
  <div class="abs center quote-mark">&ldquo;</div>
  <div class="abs client-photo" style="left:77px;top:161px" role="img" aria-label="Portrait photograph of a male client"></div>
  <div class="abs client-text" style="left:216px;top:160px">
    <p>Lorem Ipsum is dummy text of the printing and typesetting industry. Lorem Ipsum has been the industry's standard dummy text.</p>
    <p class="client-name">- CLIENT NAME</p>
  </div>
  <div class="abs client-photo" style="left:625px;top:161px" role="img" aria-label="Portrait photograph of a female client"></div>
  <div class="abs client-text" style="left:763px;top:160px">
    <p>Lorem Ipsum is dummy text of the printing and typesetting industry. Lorem Ipsum has been the industry's standard dummy text.</p>
    <p class="client-name">- CLIENT NAME</p>
  </div>
</section>

<section class="quote">
  <h2 class="abs center section-title"><span class="accent">GET A</span> FREE QUOTE</h2>
  <div class="abs field" style="left:187px;top:111px;width:364px;height:46px">Enter name</div>
  <div class="abs field" style="left:187px;top:178px;width:364px;height:48px">Enter Email</div>
  <div class="abs field" style="left:187px;top:247px;width:364px;height:46px">Enter Contact No.</div>
  <div class="abs field" style="left:571px;top:111px;width:438px;height:182px">Enter message</div>
  <div class="abs btn">SUBMIT</div>
</section>

<footer class="footer">
  <div class="abs brand" style="left:80px;top:58px">
    <div class="brand-name">Marcus Delbridge</div>
    <div class="brand-sub">Finance</div>
  </div>
  <div class="abs footer-info">
    <p>Lorem Ipsum is dummy text of the printing.</p>
    <p>Tel : <b>123 456 7890</b></p>
    <p>Email : info@marcusdelbridge.com</p>
  </div>
  <div class="abs follow-title">FOLLOW US</div>
  <div class="abs social filled" style="left:799px" role="img" aria-label="Social profile link"></div>
  <div class="abs social" style="left:862px" role="img" aria-label="Social profile link"></div>
  <div class="abs social" style="left:927px" role="img" aria-label="Social profile link"></div>
  <div class="abs footer-rule"></div>
  <p class="abs center copyright">&copy; <b>Marcus Delbridge</b> - 2017. All Rights Reserved.</p>
</footer>

</body>
</html>
```